Mandala Postcard Design

I am in need of a postcard to hand out at a Psychic Fair. I envision the card to having half-of-a Mandala (from my Facebook folder), touched up a bit to make it vibrant and bold. Others vendors will have cards w/photographic backgrounds doing yoga. I'd like mine to stand out for it's line-drawn "cartoonish" nature, solid-color nature. The wording would be my basic contact info and a short description ... something like: "Experience the Magic of Mandala Making ... Next Class will be held: (open space for writing, no lines) The art is contained in this Facebook folder. Lots to choose from, with my favorites being the stronger outlined designs.

https://www.examplesocial.net/Brightorbs/media_set?set=a.20462926615637197.2184852941.783542196&type=3
Updates

I just uploaded a few new drawings that might work better, since they are more round. I want to minimize the white space, for instance, avoid having the left & right corners empty. Another idea could be to use 1/4 mandalas in the corners. I'm ready to make a decision. I want it to look great, but as I gain drawing experience, I'll need to update my cards. Thanks! I'm not sure if this the place for this comment, but I'll also be needing a DVD label for my tutorials, and a front page design for a mandala coloring book.

Target Market(s)

Primarily women interested in metaphysical, psychic, meditation, reiki and a basic interest in art.

Font styles to use
Serif
Sans Serif

Requirements
Should not have
• Should not be on a dark card, really should be a plain white background, it seems, in order to stand out.

```html
<!DOCTYPE html>
<html lang="en">
<head>
<meta charset="utf-8">
<title>Mandala Making Postcard</title>
<link rel="stylesheet" href="https://fonts.googleapis.com/css2?family=Dawning+of+a+New+Day&family=Arimo:wght@400&display=swap">
<style>
  :root {
    --backdrop: #ecebe7;
    --card: #ffffff;
    --ink: #2a2a2a;
    --ink-soft: #3a3a3a;
    --mandala-pink: #f3a6c4;
    --mandala-yellow: #f6ec8a;
    --mandala-aqua: #6fd0e6;
    --mandala-red: #d9263a;
    --mandala-blue: #4aa8d8;
  }
  * { box-sizing: border-box; margin: 0; padding: 0; }
  html, body {
    width: 1200px;
    height: 800px;
    overflow: hidden;
    background: var(--backdrop);
  }
  .postcard {
    position: absolute;
    left: 50px;
    top: 62px;
    width: 1100px;
    height: 675px;
    background: var(--card);
    overflow: hidden;
    box-shadow: 0 2px 10px rgba(0,0,0,0.12);
  }
  .mandala {
    position: absolute;
    border-radius: 50%;
  }
  .mandala--half-left {
    left: -180px;
    top: -12px;
    width: 700px;
    height: 700px;
    background: radial-gradient(circle at center,
      var(--mandala-yellow) 0 14%,
      var(--mandala-pink) 14% 34%,
      var(--mandala-aqua) 34% 50%,
      var(--mandala-pink) 50% 64%,
      var(--mandala-yellow) 64% 100%);
    clip-path: circle(50% at 50% 50%);
  }
  .mandala--corner-top {
    left: 780px;
    top: -150px;
    width: 360px;
    height: 360px;
    background: radial-gradient(circle at center,
      var(--mandala-pink) 0 20%,
      var(--mandala-yellow) 20% 55%,
      var(--mandala-aqua) 55% 100%);
  }
  .mandala--corner-bottom {
    left: 680px;
    top: 410px;
    width: 440px;
    height: 380px;
    background: radial-gradient(ellipse at center,
      var(--mandala-pink) 0 22%,
      var(--mandala-yellow) 22% 48%,
      var(--mandala-aqua) 48% 100%);
  }
  .headline {
    position: absolute;
    left: 459px;
    top: 200px;
    width: 600px;
    text-align: center;
    font-family: "Dawning of a New Day", cursive;
    font-weight: 400;
    font-size: 56px;
    line-height: 66px;
    color: var(--ink);
  }
  .next-class {
    position: absolute;
    left: 561px;
    top: 368px;
    font-family: "Arimo", sans-serif;
    font-size: 15px;
    color: var(--ink-soft);
  }
</style>
</head>
<body>
  <main class="postcard">
    <div class="mandala mandala--half-left" role="img" aria-label="Half of a colourful hand-drawn mandala in pink, yellow, aqua and red"></div>
    <div class="mandala mandala--corner-top" role="img" aria-label="Partial hand-drawn mandala in yellow, aqua and pink in the top corner"></div>
    <div class="mandala mandala--corner-bottom" role="img" aria-label="Partial hand-drawn mandala in aqua, pink and yellow in the bottom corner"></div>

    <h1 class="headline">Experience the Magic of<br>Mandala Making</h1>
    <p class="next-class">Next Class will be held :</p>
  </main>
</body>
</html>
```